Business Card for: Bramwell Financial Advisory Services Inc.

provide strategic financial advisory services to companies in the areas of corporate finance, mergers and acquisitions, executive coaching and strategic planning

Target Market(s)

Companies, banks, accountants, lawyers

Industry/Entity Type

High end business consulting in corporate finance, mergers and acquisitions, consulting

Contact Information for Business Card

Name of company, Name: xxxxxx xxxxxx , CEO, - phone number: 1-xxx-xxx-xxxx, - email address,

Requirements
Must have
• Must be professional and simple.
Nice to have
• simple, straight graphics, must give the impression that we are trustworthy, professional, competent
Should not have
• loud colors, loud design features

```html
<!DOCTYPE html>
<html lang="en">
<head>
<meta charset="utf-8">
<title>Bramwell Financial Advisory Services Inc. — Business Card</title>
<link rel="stylesheet" href="https://fonts.googleapis.com/css2?family=Tinos:wght@400;700&display=swap">
<style>
  :root {
    --navy: #012a6b;
    --orange: #ff6a00;
    --ink: #1a1a1a;
    --paper: #ffffff;
    --backdrop: #e6e6e6;
    --rule: #222222;
  }
  * { margin: 0; padding: 0; box-sizing: border-box; }
  html, body { width: 1200px; height: 1168px; overflow: hidden; }
  body {
    background: var(--backdrop);
    font-family: "Tinos", "Times New Roman", serif;
    color: var(--ink);
    position: relative;
  }
  .card {
    position: absolute;
    width: 811px;
    height: 462px;
    border-radius: 27px;
    overflow: hidden;
  }
  .card--front { left: 199px; top: 114px; background: var(--paper); }
  .card--back { left: 188px; top: 621px; background: var(--navy); }

  .wordmark {
    font-family: "Tinos", "Times New Roman", serif;
    font-weight: 400;
    text-transform: uppercase;
    line-height: 1;
  }
  .wordmark__name { display: block; letter-spacing: 0.04em; }
  .wordmark__sub { display: block; letter-spacing: 0.06em; }

  .card--front .wordmark {
    position: absolute;
    right: 44px;
    top: 56px;
    text-align: right;
    color: var(--navy);
  }
  .card--front .wordmark__name { font-size: 52px; }
  .card--front .wordmark__sub { font-size: 18px; margin-top: 8px; }

  .accent-bar {
    position: absolute;
    left: 0; top: 224px;
    width: 10px; height: 55px;
    background: var(--orange);
  }
  .holder {
    position: absolute;
    left: 36px; top: 218px;
  }
  .holder__name {
    font-weight: 700;
    font-size: 29px;
    color: var(--navy);
  }
  .holder__role {
    font-size: 19px;
    margin-top: 8px;
  }
  .divider {
    position: absolute;
    left: 36px; top: 306px;
    width: 728px; height: 1.5px;
    background: var(--rule);
  }
  .contacts {
    position: absolute;
    left: 36px; top: 325px;
    list-style: none;
  }
  .contacts li {
    display: flex;
    align-items: center;
    height: 30px;
    font-size: 20px;
  }
  .contacts svg { width: 22px; height: 22px; margin-right: 19px; flex: none; }
  .address {
    position: absolute;
    right: 47px; top: 345px;
    text-align: right;
    font-size: 20px;
    line-height: 30px;
    font-style: normal;
  }
  .bands {
    position: absolute;
    left: 0; bottom: 0;
    width: 811px; height: 16px;
  }

  .card--back .wordmark {
    position: absolute;
    left: 0; right: 0;
    top: 178px;
    text-align: center;
    color: var(--paper);
  }
  .card--back .wordmark__name { font-size: 72px; }
  .card--back .wordmark__sub { font-size: 25px; margin-top: 12px; }
</style>
</head>
<body>

<section class="card card--front" aria-label="Business card front">
  <div class="wordmark">
    <span class="wordmark__name">Bramwell</span>
    <span class="wordmark__sub">Financial Advisory Services Inc.</span>
  </div>

  <div class="accent-bar"></div>
  <div class="holder">
    <h1 class="holder__name">Daniel Whitcombe</h1>
    <p class="holder__role">Owner</p>
  </div>

  <div class="divider"></div>

  <ul class="contacts">
    <li>
      <svg viewBox="0 0 24 24" aria-hidden="true"><path fill="#ff6a00" d="M6.6 10.8a15 15 0 0 0 6.6 6.6l2.2-2.2a1 1 0 0 1 1-.25 11.4 11.4 0 0 0 3.6.57 1 1 0 0 1 1 1V20a1 1 0 0 1-1 1A17 17 0 0 1 3 4a1 1 0 0 1 1-1h3.5a1 1 0 0 1 1 1c0 1.25.2 2.45.57 3.57a1 1 0 0 1-.25 1z"/><path fill="none" stroke="#ff6a00" stroke-width="1.8" d="M14 3a7 7 0 0 1 7 7M14 6.5a3.5 3.5 0 0 1 3.5 3.5"/></svg>
      044-321 654 987
    </li>
    <li>
      <svg viewBox="0 0 24 24" aria-hidden="true"><rect x="1" y="5" width="22" height="14" fill="#ff6a00"/><path fill="none" stroke="#fff" stroke-width="1.6" d="M1.5 6l10.5 7.5L22.5 6"/></svg>
      info@bramwelladvisory.com
    </li>
    <li>
      <svg viewBox="0 0 24 24" aria-hidden="true"><circle cx="12" cy="12" r="11" fill="#ff6a00"/><path fill="#fff" d="M7 5.5c2 .5 3 2 2.5 3.5s-2 1.5-2 3 1.5 2 1.5 3.5S8 18 7 18.5A8 8 0 0 1 7 5.5zM14 4.3c1.5 1 1 2.5 2.5 3s3 0 3.2 2A8 8 0 0 1 17 18c-1-1.5 0-3-1.5-4s-3 .5-3.5-1.5 2-2.5 2-4-1-2-1.5-4z"/></svg>
      www.bramwelladvisory.com
    </li>
  </ul>

  <address class="address">
    421, Address line goes here<br>
    45452, Country name
  </address>

  <svg class="bands" viewBox="0 0 811 16" aria-hidden="true">
    <polygon points="0,0 400,0 412,16 0,16" fill="var(--orange)"/>
    <polygon points="407,0 811,0 811,16 419,16" fill="var(--navy)"/>
  </svg>
</section>

<section class="card card--back" aria-label="Business card back">
  <div class="wordmark">
    <span class="wordmark__name">Bramwell</span>
    <span class="wordmark__sub">Financial Advisory Services Inc.</span>
  </div>
</section>

</body>
</html>
```